Website design for legal tech start up in Switzerland (B2B)

We are for a legal tech start up in Switzerland called KOVA. We have been running since August 2016. This will be our first live website.

We need a website designed and business card design for our start-up in Switzerland. We also need the Web design to be converted into HTML and CSS files.

Function of website:
• To inform potential customers of our services
• Form a key part of our digital marketing and sales footprint.
• Branding

Please find attached logo.
Updates

Project Deadline Extended Reason: Giving us time to review submissions and provide opportunity for more submissions. Added Thursday, February 16, 2017

Project Deadline Extended
Reason: Looking for more idea's not necessarily set on blue and grey colours only.

Target Market(s)

B2B tech powered legal services.

Industry/Entity Type

Legal

Contact Information for Business Card

Lean and slick design.

Coding

Coded - Design and coding required

Number of Pages Required

5+ page

Requirements
Must have
• VERY LEAN AND CLEAN DESIGN!
• We have received many great standard designs, but we are looking for something more out-of-the box: You can get inspiration from these designs: http://www.pixelvane.com/websites/clean/
• Thanks!!
• Easy content management system
• Well structured coding for additional development
• Responsive webpage for all types of devices
• SEO optimized
• Tabs (Home, services, team, careers, blog, contact us)
• Colour scheme complementary to logo
Nice to have
• Look and Design - Approachable, High-tech, Modern
• Easy to add chat bot capability in future
Should not have
• Too busy/ too much clutter
• Not take to long to load

```html
<!DOCTYPE html>
<html lang="en">
<head>
<meta charset="utf-8">
<title>KOVA – Legal Startup</title>
<link rel="stylesheet" href="https://fonts.googleapis.com/css2?family=Domine:wght@400;700&family=Open+Sans:ital,wght@0,400;0,600;0,700;1,400&display=swap">
<style>
:root{
  --navy:#1f3d70;
  --navy-deep:#17305a;
  --ink:#333;
  --muted:#666;
  --line:#ddd;
  --paper:#fff;
  --footer:#f3f3f3;
  --dark:#1d1d1d;
}
*{box-sizing:border-box;margin:0;padding:0}
html,body{width:1200px;height:2889px;overflow:hidden}
body{font-family:"Open Sans",Arial,sans-serif;color:var(--ink);background:var(--paper);position:relative}
.serif{font-family:"Domine",Georgia,serif}
section,header,footer{position:absolute;left:0;width:1200px}

/* header */
.site-header{top:0;height:112px;background:var(--paper);box-shadow:0 1px 3px rgba(0,0,0,.08);z-index:2}
.topbar{position:absolute;right:0;top:0;width:640px;height:35px}
.topbar svg{position:absolute;left:0;top:0}
.topbar-info{position:absolute;right:22px;top:0;height:35px;display:flex;align-items:center;gap:34px;color:#fff;font-size:13px}
.topbar-info span{display:flex;align-items:center;gap:8px}
.social{display:flex;gap:7px}
.social i{display:block;width:11px;height:11px;background:#fff;border-radius:2px}
.brand{position:absolute;left:96px;top:28px;font-family:"Domine",Georgia,serif;font-weight:700;font-size:58px;letter-spacing:4px;color:#3a3a3a;line-height:1}
.main-nav{position:absolute;right:52px;top:64px;display:flex;gap:38px;font-size:16px;font-family:"Domine",Georgia,serif}
.main-nav a{color:#333;text-decoration:none;position:relative;padding-bottom:26px}
.main-nav a.active{color:var(--navy)}
.main-nav a.active::after{content:"";position:absolute;left:0;right:0;bottom:0;height:2px;background:var(--navy)}

/* hero */
.hero{top:112px;height:547px;background:linear-gradient(180deg,#2e4a78 0%,#4e6c98 40%,#6c6a6a 62%,#3b3a44 78%,#1e2a3c 100%)}
.hero-box{position:absolute;left:691px;top:185px;width:410px;height:204px;background:rgba(20,28,45,.78);padding:22px 18px}
.hero-box h1{font-family:"Domine",Georgia,serif;font-weight:700;color:#fff;font-size:40px;letter-spacing:1px;line-height:1.1}
.hero-box p{color:#fff;font-size:14px;line-height:1.6;margin-top:12px;width:350px}
.btn-outline{display:inline-block;margin-top:16px;border:1px solid #fff;color:#fff;font-size:11px;font-weight:600;padding:7px 12px;text-decoration:none}
.hero-arrow{position:absolute;top:268px}

/* services */
.services{top:659px;height:510px;text-align:center}
.section-title{font-family:"Domine",Georgia,serif;font-weight:400;font-size:34px;color:#333}
.services .section-title{margin-top:55px}
.rule{width:76px;height:2px;background:#333;margin:14px auto 0}
.lead{width:900px;margin:26px auto 0;font-size:12px;line-height:1.85;color:var(--muted)}
.service{position:absolute;top:222px;width:220px;text-align:center}
.service .icon{width:106px;height:106px;border:1.5px solid var(--navy);border-radius:50%;margin:0 auto;display:flex;align-items:center;justify-content:center}
.service h3{font-family:"Domine",Georgia,serif;font-weight:400;font-size:17px;margin-top:17px;color:#333}
.service p{font-size:12px;line-height:1.75;color:var(--muted);margin-top:8px}
.service .chev{margin-top:10px}

/* team */
.team{top:1169px;height:574px}
.team-bg{position:absolute;left:0;top:0}
.team .section-title{position:absolute;top:72px;width:100%;text-align:center;color:#fff}
.team .rule{position:absolute;top:130px;left:562px;background:#fff;margin:0}
.member{position:absolute;top:187px;width:233px;height:300px;background:#fff}
.member .photo{height:227px}
.member h3{font-family:"Domine",Georgia,serif;font-weight:400;font-size:20px;text-align:center;margin-top:16px}
.member p{font-size:10px;font-style:italic;text-align:center;color:#444;margin-top:4px}

/* blog */
.blog{top:1743px;height:524px}
.blog .section-title{position:absolute;top:62px;width:100%;text-align:center}
.post{position:absolute;top:143px;width:310px}
.post .thumb{height:188px;position:relative}
.date{position:absolute;left:0;top:0;width:48px;height:48px;background:var(--navy);color:#fff;text-align:center;font-size:16px;font-weight:700;line-height:1;padding-top:8px}
.date small{display:block;font-size:9px;font-weight:400;margin-top:4px}
.post h3{font-family:"Domine",Georgia,serif;font-size:17px;font-weight:400;margin-top:19px;color:#222}
.post p{font-size:11px;line-height:1.9;color:var(--muted);margin-top:9px}

/* testimonial */
.testimonial{top:2267px;height:275px;background:linear-gradient(180deg,#1a1a1a,#262626 50%,#141414)}
.testimonial blockquote{width:880px;margin:62px auto 0;text-align:center;color:#fff;font-family:"Domine",Georgia,serif;font-size:13.5px;line-height:1.95}
.testimonial cite{display:block;text-align:center;color:#fff;font-family:"Domine",Georgia,serif;font-style:normal;font-weight:700;font-size:17px;margin-top:18px}
.testimonial cite span{font-weight:400;font-style:italic}
.dots{display:flex;justify-content:center;gap:6px;margin-top:24px}
.dots i{display:block;width:44px;height:4px;background:#555}
.dots i.on{background:#2e7bc4}

/* footer */
.site-footer{top:2542px;height:347px;background:var(--footer)}
.footer-brand{position:absolute;left:100px;top:132px;font-family:"Domine",Georgia,serif;font-weight:700;font-size:56px;letter-spacing:4px;color:#3a3a3a;line-height:1}
.fcol{position:absolute;top:52px}
.fcol h4{font-family:"Domine",Georgia,serif;font-weight:400;font-size:21px;color:#333}
.newsletter{left:366px;width:260px}
.newsletter p{font-size:11px;line-height:1.8;color:var(--muted);margin-top:18px}
.newsletter .field{margin-top:14px;width:245px;height:42px;border:1px solid var(--line);background:#fff;font-size:11px;color:#555;padding:12px 14px}
.newsletter .submit{display:inline-block;margin-top:10px;background:var(--navy);color:#fff;font-size:12px;font-weight:600;padding:9px 16px}
.contact{left:691px;width:260px}
.contact ul{list-style:none;margin-top:14px;font-size:12px;color:var(--muted);line-height:1.6}
.contact li{display:flex;gap:12px;margin-top:12px}
.contact svg{flex:none;margin-top:2px}
.links{left:982px}
.links ul{list-style:none;margin-top:16px;font-size:11px;color:#555}
.links li{margin-top:7px;display:flex;align-items:center;gap:8px}
.links li::before{content:"";border-left:4px solid #555;border-top:3px solid transparent;border-bottom:3px solid transparent}
.copyright{position:absolute;left:0;right:0;top:289px;border-top:1px solid var(--line);text-align:center;font-size:11px;color:#555;padding-top:22px}
</style>
</head>
<body>

<header class="site-header">
  <div class="topbar">
    <svg width="640" height="35" aria-hidden="true"><polygon points="0,0 640,0 640,35 30,35" fill="#1f3d70"/></svg>
    <div class="topbar-info">
      <span><svg width="12" height="12" viewBox="0 0 24 24"><path d="M6 2l4 4-2 3c1 3 4 6 7 7l3-2 4 4-3 4C10 22 2 14 2 5z" fill="#fff"/></svg>+41 44 555 0192</span>
      <span><svg width="14" height="11" viewBox="0 0 14 11"><rect x=".5" y=".5" width="13" height="10" fill="none" stroke="#fff"/><path d="M.5 .5L7 6 13.5 .5" fill="none" stroke="#fff"/></svg>Email: info@kova.ch</span>
      <span class="social"><i></i><i></i><i></i><i></i></span>
    </div>
  </div>
  <div class="brand">KOVA</div>
  <nav class="main-nav">
    <a class="active" href="#">Home</a><a href="#">Services</a><a href="#">Team</a><a href="#">Careers</a><a href="#">Blog</a><a href="#">Contact Us</a>
  </nav>
</header>

<section class="hero" role="img" aria-label="Evening city view with a stone bridge, lit street lamp and church spires over a river">
  <svg class="hero-arrow" style="left:42px" width="16" height="24" aria-hidden="true"><path d="M12 3L4 12l8 9" stroke="#fff" stroke-width="3" fill="none"/></svg>
  <svg class="hero-arrow" style="left:1142px" width="16" height="24" aria-hidden="true"><path d="M4 3l8 9-8 9" stroke="#fff" stroke-width="3" fill="none"/></svg>
  <div class="hero-box">
    <h1>LEGAL STARTUP</h1>
    <p>Sed ut perspiciatis unde omnis iste natus error sit voluptatem accusantium doloremque</p>
    <a class="btn-outline" href="#">READ MORE &#10140;</a>
  </div>
</section>

<section class="services">
  <h2 class="section-title">Our Services</h2>
  <div class="rule"></div>
  <p class="lead">Sed ut perspiciatis unde omnis iste natus error sit voluptatem accusantium doloremque laudantium, totam rem aperiam, eaque ipsa quae ab illo inventore veritatis et quasi architecto beatae vitae dicta sunt explicabo. Nemo enim ipsam voluptatem quia voluptas sit aspernatur</p>

  <div class="service" style="left:96px">
    <div class="icon"><svg width="44" height="48" viewBox="0 0 44 48"><path d="M4 2h24l8 8v36H4z" fill="#1f3d70"/><path d="M10 16h18M10 23h18M10 30h12" stroke="#fff" stroke-width="2.5"/><path d="M28 42l12-14 4 4-12 14-6 2z" fill="#1f3d70" stroke="#fff" stroke-width="1.5"/></svg></div>
    <h3>Advertising Law</h3>
    <p>Sed ut perspiciatis unde omnis iste natus error sit voluptatem accusantium dolque laudantium, totam rem</p>
    <svg class="chev" width="14" height="14" aria-hidden="true"><path d="M2 2l5 5 5-5M2 7l5 5 5-5" stroke="#333" fill="none" stroke-width="1.5"/></svg>
  </div>
  <div class="service" style="left:360px">
    <div class="icon"><svg width="40" height="42" viewBox="0 0 40 42"><circle cx="20" cy="11" r="10" fill="#1f3d70"/><path d="M2 42c0-12 8-18 18-18s18 6 18 18z" fill="#1f3d70"/></svg></div>
    <h3>Employment Law</h3>
    <p>Sed ut perspiciatis unde omnis iste natus error sit voluptatem accusantium dolque laudantium, totam rem</p>
    <svg class="chev" width="14" height="14" aria-hidden="true"><path d="M2 2l5 5 5-5M2 7l5 5 5-5" stroke="#333" fill="none" stroke-width="1.5"/></svg>
  </div>
  <div class="service" style="left:622px">
    <div class="icon"><svg width="48" height="46" viewBox="0 0 48 46"><path d="M24 2L6 18h5v14h26V18h5z" fill="#1f3d70"/><rect x="20" y="22" width="8" height="10" fill="#fff"/><path d="M2 34c8 0 12 4 20 4h16l8-6v6l-10 8H2z" fill="#1f3d70"/></svg></div>
    <h3>Commercial Law</h3>
    <p>Sed ut perspiciatis unde omnis iste natus error sit voluptatem accusantium dolque laudantium, totam rem</p>
    <svg class="chev" width="14" height="14" aria-hidden="true"><path d="M2 2l5 5 5-5M2 7l5 5 5-5" stroke="#333" fill="none" stroke-width="1.5"/></svg>
  </div>
  <div class="service" style="left:884px">
    <div class="icon"><svg width="44" height="44" viewBox="0 0 44 44"><path d="M20 4A18 18 0 1 0 38 24H20z" fill="#1f3d70"/><path d="M24 0A18 18 0 0 1 42 18H24z" fill="#1f3d70"/></svg></div>
    <h3>Financial Services</h3>
    <p>Sed ut perspiciatis unde omnis iste natus error sit voluptatem accusantium dolque laudantium, totam rem</p>
    <svg class="chev" width="14" height="14" aria-hidden="true"><path d="M2 2l5 5 5-5M2 7l5 5 5-5" stroke="#333" fill="none" stroke-width="1.5"/></svg>
  </div>
</section>

<section class="team">
  <svg class="team-bg" width="1200" height="574" role="img" aria-label="Navy band over a faint city photograph"><polygon points="0,46 600,0 1200,46 1200,574 0,574" fill="#1f3d70"/><rect x="0" y="90" width="1200" height="484" fill="#2a4a80" opacity=".35"/></svg>
  <h2 class="section-title">Our Team</h2>
  <div class="rule"></div>
  <article class="member" style="left:98px"><div class="photo" role="img" aria-label="Portrait of Lena M" style="background:linear-gradient(160deg,#c9c2b8,#8a6a55)"></div><h3>Lena M</h3><p>CEO-Sed ut perspiciatis unde</p></article>
  <article class="member" style="left:354px"><div class="photo" role="img" aria-label="Portrait of Paul Reis" style="background:linear-gradient(160deg,#bdb4ab,#3f3a38)"></div><h3>Paul Reis</h3><p>CEO-Sed ut perspiciatis unde</p></article>
  <article class="member" style="left:611px"><div class="photo" role="img" aria-label="Portrait of Nora" style="background:linear-gradient(160deg,#b8a89a,#a8323a)"></div><h3>Nora</h3><p>CEO-Sed ut perspiciatis unde</p></article>
  <article class="member" style="left:867px"><div class="photo" role="img" aria-label="Portrait of Adrian K. Weber" style="background:linear-gradient(160deg,#e6e4e0,#4b4742)"></div><h3>Adrian K. Weber</h3><p>CEO-Sed ut perspiciatis unde</p></article>
</section>

<section class="blog">
  <h2 class="section-title">Latest Blog</h2>
  <article class="post" style="left:98px">
    <div class="thumb" role="img" aria-label="Business people reviewing a folder at a meeting" style="background:linear-gradient(135deg,#d8b44a,#3b3f4a 45%,#2a2f3a)"><div class="date">02<small>JUN</small></div></div>
    <h3>Lorem ipsum dolor sit amet,</h3>
    <p>Lorem ipsum dolor sit amet, consectetur adipiscing elit. Sed blandit massa vel mauris sollicitudin dignissim. Lorem ipsum dolor sit amet, consectetur</p>
  </article>
  <article class="post" style="left:445px">
    <div class="thumb" role="img" aria-label="Hands signing documents on a desk" style="background:linear-gradient(135deg,#9aa7b8,#e6e8ec 45%,#2b3342)"><div class="date">02<small>JUN</small></div></div>
    <h3>Lorem ipsum dolor sit amet,</h3>
    <p>Lorem ipsum dolor sit amet, consectetur adipiscing elit. Sed blandit massa vel mauris sollicitudin dignissim. Lorem ipsum dolor sit amet, consectetur</p>
  </article>
  <article class="post" style="left:792px">
    <div class="thumb" role="img" aria-label="Fountain pen and sealed certificate on a dark surface" style="background:linear-gradient(135deg,#3a3a3a,#d8d6d2 55%,#2a2a2a)"><div class="date">02<small>JUN</small></div></div>
    <h3>Lorem ipsum dolor sit amet,</h3>
    <p>Lorem ipsum dolor sit amet, consectetur adipiscing elit. Sed blandit massa vel mauris sollicitudin dignissim. Lorem ipsum dolor sit amet, consectetur</p>
  </article>
</section>

<section class="testimonial" role="region" aria-label="Client testimonial">
  <blockquote>&#8220; Lorem ipsum dolor sit amet, consectetur adipiscing elit, sed do eiusmod tempor incididunt ut labore et dolore magna aliqua. Ut enim ad minim veniam, quis nostrud exercitation ullamco laboris nisi ut aliquip ex ea commodo consequat. Duis aute irure dolor in reprehenderit in voluptate velit esse cillum dolore eu fugiat nulla pariatur. Excepteur sint occaecat &#8221;</blockquote>
  <cite>Paul Reis - <span>Kova</span></cite>
  <div class="dots"><i class="on"></i><i></i><i></i></div>
</section>

<footer class="site-footer">
  <div class="footer-brand">KOVA</div>
  <div class="fcol newsletter">
    <h4>Sign up for newsletter</h4>
    <p>Excepteur sint occaecat cupidatat non proident, sunt in culpa qui officia deserunt</p>
    <div class="field">Enter email</div>
    <span class="submit">SUBSCRIPTION</span>
  </div>
  <div class="fcol contact">
    <h4>Contact Us</h4>
    <ul>
      <li><svg width="12" height="16" viewBox="0 0 12 16"><path d="M6 0a6 6 0 0 1 6 6c0 4-6 10-6 10S0 10 0 6a6 6 0 0 1 6-6z" fill="#555"/><circle cx="6" cy="6" r="2" fill="#f3f3f3"/></svg><span>Kova legal startup<br>24 Seefeldstrasse, Suite 300,<br>Zurich 8008</span></li>
      <li><svg width="12" height="12" viewBox="0 0 24 24"><path d="M6 2l4 4-2 3c1 3 4 6 7 7l3-2 4 4-3 4C10 22 2 14 2 5z" fill="#555"/></svg><span style="font-size:14px">Phone: &nbsp;(044) 555-0193</span></li>
      <li><svg width="12" height="10" viewBox="0 0 12 10"><rect width="12" height="10" fill="#555"/><path d="M0 0l6 5 6-5" stroke="#f3f3f3" fill="none"/></svg><span>Email: info@kova.ch</span></li>
    </ul>
  </div>
  <div class="fcol links">
    <h4>Quick Links</h4>
    <ul><li>Home</li><li>Services</li><li>Team</li><li>Careers</li><li>Blog</li><li>Contact Us</li></ul>
  </div>
  <div class="copyright">&copy;2016 - 2017 Kova . All Rights Reserved.</div>
</footer>

</body>
</html>
```